The Brandwell Firm

We need a new design for our letterhead and envelopes. We are a personal injury and criminal defense firm so we need something modern and clean, but more on the professional/traditional side. Our new logo has two colors and is attached to the file so we need something that works well with those colors/matches the design. The following information needs to be on the letterhead:
Phone: (555) 214-3370
Fax: (555) 214-5186
Toll-Free: (888) 431-2059
Post Office Box 4721
Millbrook, SC 29555-4721
HarmClaimCounsel.example
PalmettoTrialAdvocates.example

Target Market(s)

Clients, government agencies, other law firms

Industry/Entity Type

Legal

Font styles to use
Sans Serif
Other font styles liked:
• Arial

Colors

Designer to choose colors to be used in the design.

Requirements
Must have
• Must look professional and clean, modern
Nice to have
• I would like to see a design that works with the logo but does not distract from the content that will be printed on it
Should not have
• Too many colors or crazy designs.

```html
<!DOCTYPE html>
<html lang="en">
<head>
<meta charset="utf-8">
<title>The Brandwell Firm — Letterhead and Envelopes</title>
<link rel="stylesheet" href="https://fonts.googleapis.com/css2?family=Open+Sans:wght@400;600&display=swap">
<style>
  :root {
    --canvas: #dedede;
    --paper: #f1f1f1;
    --paper-edge: #d2d2d2;
    --brand-navy: #27308a;
    --brand-red: #cf2a27;
    --text: #6a6a6a;
    --text-dark: #3f3f3f;
    --ink: #2b2f8c;
  }
  * { box-sizing: border-box; margin: 0; padding: 0; }
  html, body { width: 1200px; height: 810px; overflow: hidden; }
  body {
    background: var(--canvas);
    font-family: "Open Sans", Arial, sans-serif;
    color: var(--text);
    position: relative;
  }

  /* Letterhead sheet */
  .letterhead {
    position: absolute; left: 137px; top: 110px;
    width: 436px; height: 614px;
    background: var(--paper);
    border: 1px solid var(--paper-edge);
  }
  .brand {
    position: absolute;
    display: flex; align-items: center; gap: 7px;
    font-weight: 600; color: var(--brand-navy);
    white-space: nowrap;
  }
  .brand-square { background: var(--brand-red); flex: none; }
  .letterhead .brand { left: 38px; top: 74px; font-size: 17px; }
  .letterhead .brand-square { width: 12px; height: 12px; }

  .contact {
    position: absolute; left: 308px; top: 56px;
    font-size: 7.2px; line-height: 9.4px; color: var(--text-dark);
  }
  .contact-lines { margin-top: 6px; display: grid; grid-template-columns: 32px 8px auto; }
  .contact-label { color: var(--brand-navy); font-weight: 600; }

  .recipient {
    position: absolute; left: 38px; top: 202px;
    font-size: 7.6px; line-height: 11.4px;
  }
  .letter-body {
    position: absolute; left: 38px; top: 270px; width: 362px;
    font-size: 7.4px; line-height: 11.4px; text-align: justify;
  }
  .letter-body p + p { margin-top: 23px; }

  .signature {
    position: absolute; left: 38px; top: 436px;
    width: 84px; height: 54px;
    background: linear-gradient(135deg, rgba(43,47,140,0.12), rgba(43,47,140,0.04));
  }
  .sign-title {
    position: absolute; left: 37px; top: 505px;
    font-size: 7.6px;
  }
  .footer-links {
    position: absolute; left: 0; right: 0; top: 585px;
    text-align: center; font-size: 7.4px; color: var(--text-dark);
  }
  .footer-links .divider { color: var(--brand-navy); margin: 0 5px; font-weight: 600; }

  /* Envelopes */
  .envelope {
    position: absolute; background: var(--paper);
    border: 1px solid var(--paper-edge);
  }
  .envelope-back { left: 619px; top: 194px; width: 444px; height: 221px; }
  .envelope-front { left: 618px; top: 444px; width: 445px; height: 221px; }
  .flap { position: absolute; left: 0; top: 0; }
  .envelope-back .brand {
    left: 0; right: 0; top: 28px; justify-content: center; font-size: 9px;
  }
  .envelope-back .brand-square { width: 7px; height: 7px; }
  .envelope-front .brand { left: 24px; top: 52px; font-size: 15px; }
  .envelope-front .brand-square { width: 11px; height: 11px; }
  .return-address {
    position: absolute; left: 24px; top: 95px;
    font-size: 7px; line-height: 9.6px; color: var(--text-dark);
  }
</style>
</head>
<body>

  <section class="letterhead" aria-label="Letterhead">
    <div class="brand"><span class="brand-square"></span>The Brandwell Firm</div>

    <address class="contact" style="font-style:normal">
      <div>Post Office Box 4721</div>
      <div>Millbrook, SC 29555-4721</div>
      <div class="contact-lines">
        <span class="contact-label">Phone</span><span>:</span><span>(555) 214-3370</span>
        <span class="contact-label">Fax</span><span>:</span><span>(555) 214-5186</span>
        <span class="contact-label">Toll-Free</span><span>:</span><span>(888) 431-2059</span>
      </div>
    </address>

    <div class="recipient">
      <div>Dear Halvorsen</div>
      <div>Keystone Print Works Corporation</div>
      <div>Department Design</div>
    </div>

    <div class="letter-body">
      <p>Lorem ipsum dolor sit amet, consectetuer adipiscing elit. Aenean commodo ligula eget dolor. Aenean massa. Cum sociis natoque penatibus et magnis dis parturient montes, nascetur ridiculus mus. Donec quam felis, ultricies nec, pellentesque eu, pretium quis, sem. Nulla consequat massa quis enim. Donec pede justo, fringilla vel, aliquet nec, vulputate eget, arcu. In enim justo, rhoncus ut, imperdiet a, venenatis vitae, justo. Nullam dictum felis eu pede mollis pretium. Integer tincidunt. Cras dapibus. Vivamus elementum semper nisi.Nullam dictum felis eu pede mollis pretium. Integer tincidunt. Cras dapibus. Vivamus elementum semper nisi.felis eu pede mollis pretium. Integer tincidunt. Cras dapibus.</p>
      <p>Quisque rutrum. Aenean imperdiet. Etiam ultricies nisi vel augue. Curabitur ullamcorper ultricies nisi. Nam eget dui. Etiam rhoncus. Maecenas tempus, tellus eget condimentum rhoncus, sem quam semper libero, sit amet adipiscing sem neque sed ipsum.felis pede mollis pretium. I am tincidunt. Cras dapibus.</p>
    </div>

    <div class="signature" role="img" aria-label="Handwritten signature in blue ink"></div>
    <div class="sign-title">Director/Excecutive Director</div>

    <div class="footer-links">www.HarmClaimCounsel.example<span class="divider">|</span>www.PalmettoTrialAdvocates.example</div>
  </section>

  <section class="envelope envelope-back" aria-label="Envelope back">
    <svg class="flap" width="444" height="70" viewBox="0 0 444 70" aria-hidden="true">
      <path d="M0 0 H444 L433 62 Q432 66 427 66 H17 Q12 66 11 62 Z" fill="#ededed" stroke="#d4d4d4" stroke-width="1"/>
    </svg>
    <div class="brand"><span class="brand-square"></span>The Brandwell Firm</div>
  </section>

  <section class="envelope envelope-front" aria-label="Envelope front">
    <div class="brand"><span class="brand-square"></span>The Brandwell Firm</div>
    <div class="return-address">
      <div>Post Office Box 4721</div>
      <div>Millbrook, SC 29555-4721</div>
    </div>
  </section>

</body>
</html>
```